Business card for medical clinic

I need an upmarket, modern medical/health business card for my clinic

Contact Information for Business Card

name, address, email, qr code

```html
<!DOCTYPE html>
<html lang="en">
<head>
<meta charset="utf-8">
<title>Alder Health Partners – Business Card</title>
<link href="https://fonts.googleapis.com/css2?family=Poppins:wght@300;400;500;600;700&display=swap" rel="stylesheet">
<style>
  :root {
    --backdrop: #222222;
    --card: #ffffff;
    --sky: #29a8e0;
    --ocean: #1f6fa8;
    --navy: #1c2a4f;
    --ink: #111111;
    --rule: #2c4a6e;
  }
  * { box-sizing: border-box; margin: 0; padding: 0; }
  html, body { width: 1200px; height: 711px; overflow: hidden; }
  body {
    background: var(--backdrop);
    font-family: "Poppins", sans-serif;
    position: relative;
  }
  .card {
    position: absolute;
    top: 200px;
    width: 540px;
    height: 309px;
    background: var(--card);
    overflow: hidden;
  }
  .card--front { left: 45px; }
  .card--back { left: 615px; }

  .brand {
    position: absolute;
    display: flex;
    align-items: center;
    gap: 12px;
  }
  .card--front .brand { left: 50%; top: 50%; transform: translate(-50%, -50%); }
  .card--back .brand { left: 26px; top: 112px; }
  .brand__dot {
    width: 34px; height: 34px;
    border: 3px solid var(--ocean);
    border-radius: 50%;
    flex: none;
  }
  .brand__name {
    color: var(--ocean);
    font-weight: 600;
    font-size: 22px;
    letter-spacing: 1.5px;
    line-height: 1.1;
    text-transform: uppercase;
  }
  .card--back .brand__dot { width: 26px; height: 26px; }
  .card--back .brand__name { font-size: 16px; letter-spacing: 1px; }

  .divider {
    position: absolute;
    left: 250px; top: 40px;
    width: 1px; height: 170px;
    background: var(--rule);
  }
  .person {
    position: absolute;
    left: 272px; top: 46px;
  }
  .person__name {
    font-size: 28px;
    line-height: 1.1;
    color: var(--sky);
  }
  .person__first { font-weight: 700; }
  .person__last { font-weight: 300; }
  .person__role {
    font-size: 12px;
    font-weight: 600;
    color: var(--ink);
    margin-top: 2px;
  }
  .contacts {
    list-style: none;
    margin-top: 16px;
  }
  .contacts li {
    display: flex;
    align-items: center;
    gap: 8px;
    font-size: 13px;
    color: var(--ink);
    line-height: 1.75;
  }
  .contacts svg { width: 14px; height: 14px; flex: none; }

  .address-band {
    position: absolute;
    left: 0; right: 0; bottom: 18px;
    height: 32px;
    background: linear-gradient(90deg, var(--sky) 0%, var(--ocean) 45%, var(--navy) 80%);
    display: flex;
    align-items: center;
    padding-left: 32px;
    color: #fff;
    font-size: 12.5px;
    letter-spacing: .3px;
  }
  .address-band__ring {
    position: absolute;
    right: 28px; top: 50%;
    transform: translateY(-50%);
    width: 48px; height: 48px;
    border: 3px solid var(--sky);
    border-radius: 50%;
    background: var(--card);
  }
</style>
</head>
<body>
  <section class="card card--front" aria-label="Card front">
    <div class="brand">
      <span class="brand__dot"></span>
      <span class="brand__name">Alder Health<br>Partners</span>
    </div>
  </section>

  <section class="card card--back" aria-label="Card back">
    <div class="brand">
      <span class="brand__dot"></span>
      <span class="brand__name">Alder Health<br>Partners</span>
    </div>

    <div class="divider"></div>

    <div class="person">
      <h1 class="person__name"><span class="person__first">Marta</span> <span class="person__last">Kovacs</span></h1>
      <p class="person__role">Founder &amp; CEO</p>
      <ul class="contacts">
        <li>
          <svg viewBox="0 0 24 24" aria-hidden="true"><path fill="#1f6fa8" d="M6.6 10.8a15.1 15.1 0 0 0 6.6 6.6l2.2-2.2a1 1 0 0 1 1-.25 11.4 11.4 0 0 0 3.6.57 1 1 0 0 1 1 1V20a1 1 0 0 1-1 1A17 17 0 0 1 3 4a1 1 0 0 1 1-1h3.5a1 1 0 0 1 1 1c0 1.25.2 2.45.57 3.57a1 1 0 0 1-.25 1z"/></svg>
          (555) 014-2290
        </li>
        <li>
          <svg viewBox="0 0 24 24" aria-hidden="true"><rect x="2" y="5" width="20" height="14" rx="2" fill="#1f6fa8"/><path d="M3 6l9 7 9-7" fill="none" stroke="#fff" stroke-width="1.8"/></svg>
          info@yourwebsite.com
        </li>
        <li>
          <svg viewBox="0 0 24 24" aria-hidden="true"><circle cx="12" cy="12" r="10" fill="#1f6fa8"/><path d="M2 12h20M12 2c3 3 3 17 0 20M12 2c-3 3-3 17 0 20" fill="none" stroke="#fff" stroke-width="1.4"/></svg>
          www.yourwebsite.com
        </li>
      </ul>
    </div>

    <div class="address-band">
      1840 Meadowbrook Ave. Suite 310 Riverton, TX 75010
      <span class="address-band__ring"></span>
    </div>
  </section>
</body>
</html>
```